Varnik Holdings — Business Card Design Brief
Overview
Design a double-sided business card for Varnik Holdings that highlights our two service arms: Varnik Communications (telecommunications) and Varnik Energy (business energy solutions). The card should feel smart and stand out when handed to clients.

Objectives
Showcase our areas of specialty clearly.
Reflect the overall Varnik / Varnik Holdings brand while acknowledging both arms.
Explore using both logos (Communications + Energy) or one unified logo, depending on the design.

Deliverables
One double-sided business card design (front + back).

Content & Copy
Front (preferred): Logo: Varnik / Varnik Holdings
Descriptor: Business Communications | Business Energy
Back:My contact details and company details
Core products: Business Mobile • Telephony • Internet • Business Energy Solutions

Brand & Visual Direction
We have a group logo currently tailored more toward telecoms, plus a separate Varnik Energy logo.
Please explore layouts that use both logos or just one, whichever works best.
Color: I wouldn't mind seeing an option using our the Blue/Purple gradient from our website (varnik-example.co.uk), but also open to non-gradient approaches and other colours..

Overall look: Smart, modern, and distinctive.
Format & Print Specs
Double-sided business card format. (Use a standard size

Must-Haves
Front: Varnik wording or Varnik Holdings wording with atleast 1 logo also on front “Business Communications | Business Energy.”

Back: Contact + company details and core products.
A design that stands out while remaining professional.

Nice-to-Have Options
A gradient version using our site’s Blue/Purple gradient.
A non-gradient version.
A dual-logo treatment versus a single-logo treatment.

Thanks
Owen

```html
<!DOCTYPE html>
<html lang="en">
<head>
<meta charset="utf-8">
<title>Varnik Holdings — Business Card</title>
<link rel="stylesheet" href="https://fonts.googleapis.com/css2?family=Montserrat:wght@400;500;600;800&display=swap">
<style>
  :root {
    --bg: #b9b9b9;
    --navy: #24205e;
    --ink: #2b2b3a;
    --accent-blue: #1f9ad6;
    --grad-purple: #7a4a9f;
    --grad-blue: #1f66a6;
    --divider-green: #5dac3c;
    --white: #ffffff;
    --circle-comms: #27a3df;
    --circle-energy: #8cc63f;
  }
  * { box-sizing: border-box; margin: 0; padding: 0; }
  html, body { width: 1200px; height: 802px; overflow: hidden; }
  body {
    background: var(--bg);
    font-family: "Montserrat", sans-serif;
    display: flex;
    align-items: center;
    justify-content: center;
    gap: 40px;
  }
  .card {
    position: relative;
    width: 530px;
    height: 303px;
    border-radius: 22px;
    overflow: hidden;
    box-shadow: 0 10px 28px rgba(0,0,0,0.25);
  }

  /* Contact side */
  .card--contact { background: var(--white); color: var(--ink); }
  .contact__wordmark {
    position: absolute; left: 48px; top: 40px;
    font-weight: 800; font-size: 58px; letter-spacing: 1px;
    color: var(--navy);
  }
  .contact__marker {
    position: absolute; left: 0; top: 118px;
    width: 22px; height: 36px; background: var(--accent-blue);
  }
  .contact__details { position: absolute; left: 48px; top: 118px; }
  .contact__name {
    font-weight: 800; font-size: 19px; color: var(--navy); letter-spacing: 0.5px;
  }
  .contact__role { font-size: 13px; margin-bottom: 8px; }
  .contact__address { font-size: 13px; line-height: 1.35; margin-bottom: 6px; }
  .contact__list { list-style: none; font-size: 13px; line-height: 1.45; }
  .contact__list li { display: flex; align-items: center; gap: 8px; }
  .contact__icon { width: 11px; height: 11px; flex: none; }
  .contact__band {
    position: absolute; left: 0; right: 0; bottom: 0; height: 36px;
    background: var(--navy); color: var(--white);
    display: flex; align-items: center; justify-content: center; gap: 8px;
    font-size: 13px; font-weight: 500;
  }
  .contact__band .dot { color: var(--accent-blue); font-weight: 800; }

  /* Brand side */
  .card--brand {
    background: linear-gradient(100deg, var(--grad-purple) 0%, #5a5aa0 45%, var(--grad-blue) 100%);
    color: var(--white);
    display: flex; align-items: center;
  }
  .brand__arm {
    flex: 1; display: flex; flex-direction: column; align-items: center;
  }
  .brand__mark { display: flex; align-items: center; gap: 10px; }
  .brand__dot { width: 30px; height: 30px; border-radius: 50%; }
  .brand__dot--comms { background: var(--circle-comms); }
  .brand__dot--energy { background: var(--circle-energy); }
  .brand__name { font-weight: 800; font-size: 40px; letter-spacing: 1px; }
  .brand__descriptor { margin-top: 34px; font-weight: 600; font-size: 15px; letter-spacing: 0.3px; }
  .brand__divider { width: 1px; height: 150px; background: var(--divider-green); }
</style>
</head>
<body>

  <section class="card card--contact" aria-label="Contact side">
    <div class="contact__wordmark">VARNIK</div>
    <div class="contact__marker"></div>
    <div class="contact__details">
      <p class="contact__name">DELWYN MARSH</p>
      <p class="contact__role">Founder/CEO</p>
      <p class="contact__address">24 Alder Row, Brackford<br>England, BK2 7QP</p>
      <ul class="contact__list">
        <li>
          <svg class="contact__icon" viewBox="0 0 12 12" aria-hidden="true"><path d="M2.5 1 L4.5 1 L5.2 3.5 L4 4.5 Q5 7 7.5 8 L8.5 6.8 L11 7.5 L11 9.5 Q10 11 8 10.8 Q2 9.5 1 3.5 Q1 1.8 2.5 1Z" fill="var(--accent-blue)"/></svg>
          +44 0100 555 0192
        </li>
        <li>
          <svg class="contact__icon" viewBox="0 0 12 12" aria-hidden="true"><rect x="0.5" y="2" width="11" height="8" rx="1" fill="var(--accent-blue)"/><path d="M1 2.5 L6 6.5 L11 2.5" stroke="#fff" stroke-width="1" fill="none"/></svg>
          info@varnik-example.co.uk
        </li>
        <li>
          <svg class="contact__icon" viewBox="0 0 12 12" aria-hidden="true"><circle cx="6" cy="6" r="5.3" fill="var(--accent-blue)"/><path d="M0.8 6 H11.2 M6 0.8 Q3 6 6 11.2 M6 0.8 Q9 6 6 11.2" stroke="#fff" stroke-width="0.8" fill="none"/></svg>
          www.varnik-example.co.uk
        </li>
      </ul>
    </div>
    <div class="contact__band">
      <span>Business Mobile</span><span class="dot">•</span>
      <span>Telephony</span><span class="dot">•</span>
      <span>Internet</span><span class="dot">•</span>
      <span>Business Energy Solutions</span>
    </div>
  </section>

  <section class="card card--brand" aria-label="Brand side">
    <div class="brand__arm">
      <div class="brand__mark">
        <span class="brand__dot brand__dot--comms"></span>
        <span class="brand__name">VARNIK</span>
      </div>
      <p class="brand__descriptor">Business Communications</p>
    </div>
    <div class="brand__divider"></div>
    <div class="brand__arm">
      <div class="brand__mark">
        <span class="brand__dot brand__dot--energy"></span>
        <span class="brand__name">VARNIK</span>
      </div>
      <p class="brand__descriptor">Business Energy</p>
    </div>
  </section>

</body>
</html>
```